Popup Nightclub Grand Opening Flyer

We need to design a flyer for the grand opening of an upscale, exclusive nightclub called "Lantern". The design needs to be chic and exclusive. The background should be black and the text should primarily be white. We like minimalist designs.

Here is the text for the flyer
-
Velvetroll Atlanta Presents

Lantern (LOGO)

A Popup Nightclub Experience
For one night Only

Friday, October 18, 2013
Party begins at 9PM

INVITE ONLY

See invitation for location details
(Velvetroll Atlanta logo)

-
Examples we like

http://cdn4-x.pressfolio-example.com/sites/default/files/styles/image_content_width/hash/3b/fd/2468013579_4421_flyer.jpg?itok=K9rtQw2z

http://files.hubspace-example.net/files/8Hqq-Tr72WWE3kaRbTmcxP5QZK2F396J8nbRw4CKMHfdX2Y7qSEF-MqjxDoNrLY3QCyQJD7npjGaRq3k-Mhx6hqf3MDSWf8r3/2zenSaturdays.jpg

http://morvex-example.com/wp-content/uploads/siteskin/widgetkit/gallery/2zen/2zen-gen_qstay4-01.jpg

Hi All, one thing that we are seeing that we don't like is on over emphasis on the phrase "a popup nightclub experience" please don't make this the largest thing on the flyer

Target Market(s)

Target market is 25-35 year olds who are affluent (rich) and like luxury brands

Requirements
Must have
• Dark Background
Nice to have
• Velvetroll Logo on the bottom
Modern text that isn't curvy
Should not have
• Curved text

```html
<!DOCTYPE html>
<html lang="en">
<head>
<meta charset="utf-8">
<title>Lantern Nightclub – Popup Opening</title>
<link rel="stylesheet" href="https://fonts.googleapis.com/css2?family=Open+Sans:wght@300;400&family=Arimo:wght@400;700&family=Tinos:wght@700&display=swap">
<style>
  :root {
    --ink: #0b0b0b;
    --weave-light: #1c1c1c;
    --weave-dark: #050505;
    --text: #ffffff;
    --text-soft: #e9e9e9;
    --band: #74c68c;
  }
  html, body {
    margin: 0;
    padding: 0;
    width: 851px;
    height: 1200px;
    overflow: hidden;
    background: var(--ink);
  }
  .flyer {
    position: relative;
    width: 851px;
    height: 1200px;
    overflow: hidden;
    color: var(--text);
  }
  .backdrop {
    position: absolute;
    inset: 0;
    background: radial-gradient(ellipse at 50% 45%, var(--weave-light) 0%, #101010 55%, var(--weave-dark) 100%);
  }
  .centered {
    position: absolute;
    transform: translateX(-50%);
    white-space: nowrap;
    margin: 0;
  }
  .presenter {
    left: 425px;
    top: 76px;
    font-family: "Open Sans", sans-serif;
    font-weight: 400;
    font-size: 31px;
    letter-spacing: 0.2px;
  }
  .band {
    position: absolute;
    left: 112px;
    width: 625px;
    background: var(--band);
  }
  .band--top { top: 130px; height: 54px; }
  .band--bottom { top: 524px; height: 57px; }
  .club-mark {
    position: absolute;
    left: 425px;
    top: 222px;
    width: 112px;
    height: 112px;
    margin-left: -56px;
    border-radius: 50%;
    background: var(--text-soft);
  }
  .club-name {
    left: 425px;
    top: 396px;
    font-family: "Open Sans", sans-serif;
    font-weight: 300;
    color: var(--text-soft);
    text-align: center;
    text-transform: uppercase;
    line-height: 1;
  }
  .club-name__main {
    display: block;
    font-size: 62px;
    letter-spacing: 7px;
  }
  .club-name__sub {
    display: block;
    margin-top: 12px;
    font-size: 29px;
    letter-spacing: 4px;
  }
  .tagline {
    position: absolute;
    left: 142px;
    top: 604px;
    margin: 0;
    font-family: "Arimo", sans-serif;
    font-weight: 400;
    font-size: 22px;
    font-variant: small-caps;
    letter-spacing: 4px;
    line-height: 44px;
    color: var(--text-soft);
  }
  .tagline span { display: block; }
  .event-date, .event-time {
    font-family: "Arimo", sans-serif;
    font-weight: 700;
    font-size: 20px;
    letter-spacing: 4.5px;
    text-transform: uppercase;
    color: var(--text-soft);
  }
  .event-date { left: 442px; top: 727px; }
  .event-time { left: 460px; top: 768px; }
  .access {
    left: 421px;
    top: 848px;
    font-family: "Tinos", serif;
    font-weight: 700;
    font-size: 23px;
  }
  .location-note {
    left: 436px;
    top: 911px;
    font-family: "Arimo", sans-serif;
    font-weight: 700;
    font-size: 17px;
  }
  .host {
    position: absolute;
    left: 425px;
    top: 984px;
    transform: translateX(-50%);
    display: flex;
    align-items: center;
    gap: 22px;
    white-space: nowrap;
  }
  .host__dot {
    width: 54px;
    height: 54px;
    border-radius: 50%;
    background: var(--text);
  }
  .host__name {
    font-family: "Open Sans", sans-serif;
    font-weight: 400;
    font-size: 40px;
    letter-spacing: 3px;
    text-transform: uppercase;
    color: var(--text);
  }
</style>
</head>
<body>
  <main class="flyer">
    <div class="backdrop" role="img" aria-label="Dark woven carbon-fibre texture filling the background"></div>

    <p class="centered presenter">Velvetroll Atlanta Presents</p>

    <div class="band band--top"></div>

    <div class="club-mark"></div>
    <h1 class="centered club-name">
      <span class="club-name__main">Lantern</span>
      <span class="club-name__sub">Nightclub</span>
    </h1>

    <div class="band band--bottom"></div>

    <p class="tagline">
      <span>A Popup Nightclub Experience</span>
      <span>For one night Only</span>
    </p>

    <p class="centered event-date">Friday, October&nbsp; 18, 2013</p>
    <p class="centered event-time">Party begins at 9PM</p>

    <p class="centered access">Invite Only</p>
    <p class="centered location-note">See invitation for location details</p>

    <div class="host">
      <span class="host__dot"></span>
      <span class="host__name">Velvetroll Atlanta</span>
    </div>
  </main>
</body>
</html>
```